Fernhale Business Card Design

We are looking for a fresh business card design for our new logo. We would like a business card that is unique but friendly. We are in the window coverings business offering blinds, shutters and shades for homes.

Target Market(s)

Targeting the end-consumer

Industry/Entity Type

Business

Requirements
Must have
• Must have a dedicates space for a photo of our sales person. Must contain our new logo (attached).

```html
<!DOCTYPE html>
<html lang="en">
<head>
<meta charset="utf-8">
<title>Fernhale Business Card</title>
<link href="https://fonts.googleapis.com/css2?family=Roboto:wght@400;500&display=swap" rel="stylesheet">
<style>
  :root {
    --backdrop: #7b5539;
    --card-grey: #75767b;
    --card-white: #f4f4f4;
    --leaf-green: #7ab929;
    --text-grey: #4a4a4d;
    --title-grey: #6e6e72;
    --photo-top: #d4d4d6;
    --photo-bottom: #a9a9ad;
  }
  * { margin: 0; padding: 0; box-sizing: border-box; }
  html, body { width: 1200px; height: 960px; overflow: hidden; }
  body {
    background: var(--backdrop);
    position: relative;
    font-family: "Roboto", Arial, sans-serif;
  }
  .card {
    position: absolute;
    width: 600px;
    height: 344px;
    box-shadow: 0 3px 8px rgba(0,0,0,0.35);
  }
  .card-front { left: 314px; top: 113px; background: var(--card-grey); }
  .card-back { left: 311px; top: 471px; background: var(--card-white); }
  .front-panel {
    position: absolute;
    left: 16px; top: 15px; right: 16px; bottom: 16px;
    background: var(--card-white);
    border-radius: 48px 0 48px 0;
  }
  .back-panel {
    position: absolute;
    left: 15px; top: 15px; right: 15px; bottom: 14px;
    background: var(--card-grey);
    border-radius: 48px 0 48px 0;
  }
  .photo-slot {
    position: absolute;
    left: 243px; top: 52px;
    width: 82px; height: 109px;
    border: 1.5px solid #2a2a2a;
    border-radius: 8px;
    background: linear-gradient(180deg, var(--photo-top), var(--photo-bottom));
  }
  .contact {
    position: absolute;
    left: 0; right: 0; top: 170px;
    text-align: center;
    color: var(--text-grey);
  }
  .person-name {
    color: var(--leaf-green);
    font-size: 20px;
    font-weight: 500;
    line-height: 22px;
  }
  .person-title {
    color: var(--title-grey);
    font-size: 15px;
    line-height: 20px;
    margin-bottom: 6px;
  }
  .contact-line { font-size: 14px; line-height: 20px; }
  .label { color: var(--leaf-green); }
  .brand {
    position: absolute;
    left: 110px; top: 118px;
    display: flex; align-items: center; gap: 20px;
    color: #ffffff;
  }
  .brand-mark {
    width: 78px; height: 78px;
    border: 3px solid #ffffff;
    border-radius: 6px;
  }
  .brand-name { font-size: 50px; font-weight: 400; letter-spacing: 0.5px; }
  .back-url {
    position: absolute;
    left: 0; right: 0; top: 274px;
    text-align: center;
    color: #ececec;
    font-size: 14px;
    letter-spacing: 5px;
  }
</style>
</head>
<body>
  <section class="card card-front">
    <div class="front-panel">
      <div class="photo-slot" role="img" aria-label="Photo of the sales person"></div>
      <div class="contact">
        <p class="person-name">DANIEL MARSH</p>
        <p class="person-title">CEO/FOUNDER</p>
        <p class="contact-line">4120 Cedar Hollow Road, Juneau, Alaska 99801</p>
        <p class="contact-line"><span class="label">P:</span> 555 201 4837 <span class="label">M:</span> 555 318 7290 <span class="label">F:</span> 555 462 0915 <span class="label">E:</span> name@fernhale.com</p>
        <p class="contact-line"><span class="label">W:</span> www.fernhale.com</p>
      </div>
    </div>
  </section>

  <section class="card card-back">
    <div class="back-panel">
      <div class="brand">
        <span class="brand-mark"></span>
        <span class="brand-name">Fernhale</span>
      </div>
      <p class="back-url">www.fernhale.com</p>
    </div>
  </section>
</body>
</html>
```